RW Framewell Inc Business cards

We need business cards using our existing logo but slightly modified. Right now the logo says RW Loadbearing Masonry. We want to keep the RW part of the design, but replace the Structural Concrete portion with "FRAMEWELL". Please see the attached file.
Ideally this would be a blank template so we can add Different Names, titles, and phone numbers later.
On the one side we want only the logo and on the other side the detail. I'm attaching an example for you to see.
Please reach out with any other questions. Our address and other details will be given out once we find a design we like.

Target Market(s)

Construction Industry

```html
<!DOCTYPE html>
<html lang="en">
<head>
<meta charset="utf-8">
<title>RW Framewell Inc – Business Cards</title>
<link rel="stylesheet" href="https://fonts.googleapis.com/css2?family=Roboto:wght@400;700&display=swap">
<style>
  :root {
    --backdrop: #9c9c9c;
    --brand-blue: #0f77bf;
    --pattern-blue: #1479c2;
    --white: #ffffff;
    --accent-grey: #808285;
  }
  * { box-sizing: border-box; margin: 0; padding: 0; }
  html, body {
    width: 1021px; height: 1200px; overflow: hidden;
    background: var(--backdrop);
    font-family: "Roboto", Arial, sans-serif;
  }
  .card {
    position: absolute; left: 134px; width: 753px; height: 429px;
    overflow: hidden;
  }
  .card--front { top: 119px; background: var(--brand-blue); }
  .card--back { top: 651px; background: var(--white); }

  .front__texture {
    position: absolute; inset: 0;
    background: linear-gradient(180deg, var(--pattern-blue), var(--brand-blue));
  }
  .front__wordmark {
    position: absolute; left: 531px; top: 308px; width: 128px;
    color: var(--white); font-weight: 700; text-align: center;
  }
  .front__initials { font-size: 60px; line-height: 60px; letter-spacing: 2px; }
  .front__name { font-size: 9.5px; letter-spacing: 7.4px; margin-top: 4px; margin-right: -7px; }

  .back__logo-panel {
    position: absolute; left: 0; top: 0; width: 376px; height: 100%;
    background: var(--white);
  }
  .back__initials {
    position: absolute; left: 60px; top: 150px;
    font-size: 128px; line-height: 128px; font-weight: 700;
    color: var(--brand-blue); letter-spacing: 4px;
  }
  .back__details {
    position: absolute; left: 376px; top: 0; right: 0; height: 100%;
    background: var(--brand-blue); color: var(--white);
  }
  .back__pointer { position: absolute; left: 0; top: 96px; }
  .person { position: absolute; left: 36px; top: 96px; }
  .person__name { font-size: 27px; font-weight: 700; line-height: 32px; }
  .person__title { font-size: 17px; line-height: 22px; }
  .address { position: absolute; left: 36px; top: 175px; font-size: 17.5px; line-height: 22px; }
  .contacts { position: absolute; left: 36px; top: 254px; list-style: none; }
  .contacts li {
    display: flex; align-items: center; height: 28.5px;
    font-size: 18px;
  }
  .contacts .icon {
    width: 24px; height: 24px; border-radius: 50%;
    background: var(--accent-grey); margin-right: 8px;
    display: flex; align-items: center; justify-content: center; flex: none;
  }
</style>
</head>
<body>
  <section class="card card--front" aria-label="Card front">
    <div class="front__texture" role="img" aria-label="Faint repeated brand-mark texture across the blue background"></div>
    <div class="front__wordmark">
      <div class="front__initials">RW</div>
      <div class="front__name">FRAMEWELL</div>
    </div>
  </section>

  <section class="card card--back" aria-label="Card back">
    <div class="back__logo-panel">
      <div class="back__initials">RW</div>
    </div>
    <div class="back__details">
      <svg class="back__pointer" width="24" height="52" viewBox="0 0 24 52"><polygon points="0,0 24,26 0,52" fill="var(--accent-grey)"/></svg>
      <div class="person">
        <div class="person__name">DANIEL MERCER</div>
        <div class="person__title">Owner/CEO</div>
      </div>
      <div class="address">
        1450 N Harlow Avenue<br>Brookfield 4417
      </div>
      <ul class="contacts">
        <li><span class="icon"><svg width="10" height="14" viewBox="0 0 10 14"><rect x="1" y="0.8" width="8" height="12.4" rx="1.4" fill="none" stroke="#fff" stroke-width="1.4"/><circle cx="5" cy="11" r="0.8" fill="#fff"/></svg></span>555-014-2200</li>
        <li><span class="icon"><svg width="13" height="13" viewBox="0 0 24 24"><path d="M6.6 10.8a15.1 15.1 0 0 0 6.6 6.6l2.2-2.2a1 1 0 0 1 1-.25 11.4 11.4 0 0 0 3.6.57 1 1 0 0 1 1 1V20a1 1 0 0 1-1 1A17 17 0 0 1 3 4a1 1 0 0 1 1-1h3.5a1 1 0 0 1 1 1c0 1.25.2 2.45.57 3.57a1 1 0 0 1-.25 1z" fill="#fff"/></svg></span>555-017-8431</li>
        <li><span class="icon"><svg width="13" height="10" viewBox="0 0 13 10"><rect x="0.5" y="0.5" width="12" height="9" fill="#fff"/><polyline points="0.5,0.5 6.5,5.5 12.5,0.5" fill="none" stroke="var(--accent-grey)" stroke-width="1"/></svg></span>info@rwframewell.com</li>
        <li><span class="icon"><svg width="13" height="13" viewBox="0 0 14 14"><circle cx="7" cy="7" r="6" fill="none" stroke="#fff" stroke-width="1.4"/><ellipse cx="7" cy="7" rx="2.6" ry="6" fill="none" stroke="#fff" stroke-width="1.2"/><line x1="1" y1="7" x2="13" y2="7" stroke="#fff" stroke-width="1.2"/></svg></span>www.rwframewell.com</li>
      </ul>
    </div>
  </section>
</body>
</html>
```